New Website for World Wide Charity (KOLVAN)

We need a dynamic web design for our brand new charity organisation that will be working worldwide. We will be funded by donations so need to attract people to donate.

What We Do
We work to optimise the wellbeing of the planet, the animals and all that live within. Our slogan is Achieving Vibrational Equilibrium.

We have included a Powerpoint document which may help you understand what we need, it is just an idea for structure and style, it is not set in stone so feel free to be as creative as you like!
Updates

Designs look the same

Target Market(s)

Adults 18+ with an interest in animal, environmental. Businesses that may like to support our natural world or already support our natural world.

Number of Pages Required

3 page

Colors

Designer to choose colors to be used in the design.

Requirements
Must have
• We need the website to be easy to use and understand.

Web pages will be Home, What We Do, Who We Are, Success Stories, What You Can Do (Blog section), Seek Help, Donate, Join.
Nice to have
• Natural feel, easy to navigate, Ideally the website will look natural and organic.

Natural colours, blues, greens, sand, gold, brown, grey, silver, Orange and yellow for impact.
Should not have
• Should not have a dark coloured theme.

```html
<!DOCTYPE html>
<html lang="en">
<head>
<meta charset="utf-8">
<title>KOLVAN – Help Raise World Vibration</title>
<link href="https://fonts.googleapis.com/css2?family=Montserrat:wght@300;400;500;600&display=swap" rel="stylesheet">
<style>
:root{
  --lavender:#e8d8e6;
  --lavender-deep:#d9c3d6;
  --mist:#cdb6cc;
  --plum:#6e3a59;
  --plum-dark:#5a2c48;
  --ink:#2a2a2a;
  --white:#ffffff;
  --btn-light:#eadbe8;
  --btn-mid:#b9a4bb;
  --forest-top:#5f8a55;
  --forest-mid:#2f5a34;
  --forest-low:#1f3d26;
}
*{margin:0;padding:0;box-sizing:border-box}
html,body{width:1200px;height:3744px;overflow:hidden}
body{font-family:'Montserrat',sans-serif;color:var(--ink);background:var(--lavender);position:relative}
.page{position:relative;width:1200px;height:3744px;overflow:hidden;background:var(--lavender)}

/* header */
.site-header{position:absolute;top:0;left:0;width:1200px;height:64px;background:var(--white);z-index:5}
.nav-icon{position:absolute;left:86px;top:24px;width:26px;height:14px;border-radius:7px;background:var(--mist)}
.nav{position:absolute;top:22px;font-size:15px;font-weight:500;display:flex;gap:30px}
.nav-left{left:156px}
.nav-right{left:690px}
.brand{position:absolute;left:550px;top:4px;width:100px;height:100px;border-radius:50%;background:var(--white);border:3px solid var(--plum);display:flex;align-items:center;justify-content:center;font-size:16px;font-weight:600;color:var(--plum);letter-spacing:1px;z-index:6}
.btn{position:absolute;border-radius:22px;font-size:14px;font-weight:500;display:flex;align-items:center;justify-content:center}
.btn-donate{left:866px;top:10px;width:122px;height:42px;background:var(--btn-light);color:var(--plum-dark)}
.btn-join{left:1002px;top:10px;width:122px;height:42px;background:var(--btn-mid);color:var(--white)}

/* hero */
.hero-photo{position:absolute;top:64px;left:0;width:1200px;height:600px;background:linear-gradient(180deg,var(--forest-top) 0%,var(--forest-mid) 55%,var(--forest-low) 88%,var(--lavender) 100%)}
.hero-title{position:absolute;top:262px;left:0;width:1200px;text-align:center;color:var(--white);font-size:44px;font-weight:600;letter-spacing:4px}
.hero-text{position:absolute;top:320px;left:230px;width:740px;text-align:center;color:var(--white);font-size:15px;line-height:24px}
.btn-hero{left:512px;top:404px;width:176px;height:50px;background:var(--btn-light);color:var(--ink);font-size:15px}

/* soft backdrop bands */
.backdrop{position:absolute;left:0;width:1200px}
.backdrop-upper{top:1200px;height:950px;background:linear-gradient(180deg,var(--lavender) 0%,var(--lavender-deep) 45%,var(--lavender) 100%)}
.backdrop-lower{top:2350px;height:800px;background:linear-gradient(180deg,var(--lavender) 0%,var(--lavender-deep) 50%,var(--lavender) 100%)}

/* cards */
.cards{position:absolute;top:780px;left:90px;width:1020px;height:360px;display:flex}
.card{flex:1;position:relative;display:flex;flex-direction:column;align-items:center;justify-content:center;color:var(--white)}
.card-env{background:linear-gradient(160deg,#c9b44a,#6f8c34 60%,#3f6a2a)}
.card-animal{background:linear-gradient(180deg,#93a0ad,#c7ccd0 60%,#7d8486)}
.card-human{background:linear-gradient(160deg,#c88a3c,#a96a36 55%,#d8c1a8)}
.card-title{font-size:36px;font-weight:300;letter-spacing:2px;text-transform:uppercase}
.card-link{font-size:14px;margin-top:6px}

/* stories */
.story-title{position:absolute;font-size:52px;font-weight:400}
.story-text{position:absolute;font-size:15px;line-height:24px;width:330px}
.story-photo{position:absolute;border-radius:50%}
.photo-env{left:488px;top:1258px;width:560px;height:560px;background:radial-gradient(circle at 55% 50%,#a8d46a,#3f8a3a 55%,#1d4c24)}
.photo-animal{left:144px;top:1872px;width:566px;height:566px;background:linear-gradient(180deg,#8fb2dc,#3d6fb7 55%,#1f4a98)}
.photo-human{left:490px;top:2444px;width:560px;height:560px;background:radial-gradient(circle at 50% 55%,#f6c66a,#e08a3c 55%,#8c4a2a)}

/* footer */
.footer-trees{position:absolute;top:3160px;left:0;width:1200px;height:180px;background:linear-gradient(180deg,rgba(110,58,89,0) 0%,rgba(110,58,89,.35) 45%,var(--plum) 100%)}
.site-footer{position:absolute;top:3330px;left:0;width:1200px;height:414px;background:var(--plum);color:var(--white)}
.footer-brand{position:absolute;left:92px;top:52px;width:110px;height:110px;border-radius:50%;background:var(--white);border:3px solid var(--lavender);display:flex;align-items:center;justify-content:center;color:var(--plum);font-size:16px;font-weight:600;letter-spacing:1px}
.charity-no{position:absolute;left:60px;top:176px;width:176px;text-align:center;font-size:12px;line-height:18px;font-weight:500}
.footer-col{position:absolute;top:70px;font-size:13px;line-height:22px}
.footer-col h3{font-size:20px;font-weight:400;margin-bottom:8px}
.col-involved{left:398px}
.col-help{left:688px}
.col-legal{left:954px}
.footer-bar{position:absolute;left:0;bottom:0;width:1200px;height:44px;background:var(--plum-dark);font-size:12px;display:flex;align-items:center;justify-content:center}
.to-top{position:absolute;right:40px;top:14px;font-size:12px}
</style>
</head>
<body>
<div class="page">

  <div class="backdrop backdrop-upper" role="img" aria-label="Misty mountain landscape"></div>
  <div class="backdrop backdrop-lower" role="img" aria-label="Misty mountain landscape"></div>

  <header class="site-header">
    <span class="nav-icon"></span>
    <nav class="nav nav-left"><span>What We Do</span><span>Who We Are</span><span>Success Stories</span></nav>
    <nav class="nav nav-right"><span>What You Can Do</span></nav>
    <span class="btn btn-donate">Donate</span>
    <span class="btn btn-join">Join</span>
  </header>
  <div class="brand">KOLVAN</div>

  <section class="hero">
    <div class="hero-photo" role="img" aria-label="Evergreen forest seen from above"></div>
    <h1 class="hero-title">HELP RAISE WORLD VIBRATION</h1>
    <p class="hero-text">Lorem ipsum dolor sit amet, consectetur adipiscing elit, sed do eiusmod tempor incididunt ut labore et dolore magna aliqua. Ut enim ad minim veniam, quis nostrud exercitation ullamco laboris nisi ut aliquip.</p>
    <span class="btn btn-hero">Make A Difference</span>
  </section>

  <section class="cards">
    <div class="card card-env" role="img" aria-label="Sunlit forest"><span class="card-title">Environment</span><span class="card-link">Find Out More</span></div>
    <div class="card card-animal" role="img" aria-label="Polar bear on rocks"><span class="card-title">Animal</span><span class="card-link">Find Out More</span></div>
    <div class="card card-human" role="img" aria-label="Person breathing in sunlight"><span class="card-title">Human</span><span class="card-link">Find Out More</span></div>
  </section>

  <section class="story">
    <div class="story-photo photo-env" role="img" aria-label="Hands holding a glass globe on moss"></div>
    <h2 class="story-title" style="left:134px;top:1418px">Environment</h2>
    <p class="story-text" style="left:134px;top:1494px">Lorem ipsum dolor sit amet, consectetur adipiscing elit, sed do eiusmod tempor incididunt ut labore et dolore magna aliqua. Ut enim ad minim veniam, quis nostrud exercitation ullamco laboris nisi ut aliquip ex ea commodo consequat. Duis aute irure dolor in reprehenderit in voluptate velit esse cillum dolore.</p>
  </section>

  <section class="story">
    <div class="story-photo photo-animal" role="img" aria-label="Polar bear on sea ice"></div>
    <h2 class="story-title" style="left:740px;top:2050px">Animal</h2>
    <p class="story-text" style="left:740px;top:2124px">Lorem ipsum dolor sit amet, consectetur adipiscing elit, sed do eiusmod tempor incididunt ut labore et dolore magna aliqua. Ut enim ad minim veniam, quis nostrud exercitation ullamco laboris nisi ut aliquip ex ea commodo consequat. Duis aute irure dolor in reprehenderit in voluptate velit esse cillum dolore.</p>
  </section>

  <section class="story">
    <div class="story-photo photo-human" role="img" aria-label="Person leaping at sunset"></div>
    <h2 class="story-title" style="left:134px;top:2676px">Human</h2>
    <p class="story-text" style="left:134px;top:2752px">Lorem ipsum dolor sit amet, consectetur adipiscing elit, sed do eiusmod tempor incididunt ut labore et dolore magna aliqua. Ut enim ad minim veniam, quis nostrud exercitation ullamco laboris nisi ut aliquip ex ea commodo consequat. Duis aute irure dolor in reprehenderit in voluptate velit esse cillum dolore.</p>
  </section>

  <div class="footer-trees" role="img" aria-label="Misty pine tree line"></div>

  <footer class="site-footer">
    <div class="footer-brand">KOLVAN</div>
    <p class="charity-no">CHARITY NUMBER<br>11 1234567890</p>
    <div class="footer-col col-involved"><h3>Get Involved</h3><p>Join Us</p><p>Fundraise</p><p>Donate</p><p>Shop</p></div>
    <div class="footer-col col-help"><h3>Get Help</h3><p>Contact Us</p><p>Media</p></div>
    <div class="footer-col col-legal"><h3>Legal</h3><p>Terms and Conditions</p><p>Cookies</p><p>Privacy Policy</p></div>
    <div class="footer-bar">© 2020 The Company Name. All Rights Reserved.<span class="to-top">Top</span></div>
  </footer>

</div>
</body>
</html>
```